established boer goat stud and dorper sheep stud need an updated look

I need a design to promote the boer goat stud and dorper sheep stud, so its clear and simple
Updates

Details for business card design Wirrabel Boers and Dorper Sheep Stud. I would like silhouette animal head or full body of a boer goat (not a dairy breed goat) and Dorper sheep. Contact: Maree Dalton +61 412578304 Sandra Pollock +61 438615027 Mooroopna North Victoria Australia Email: wirrabel5184@mailvane.com

Industry/Entity Type

Agriculture

Contact Information for Business Card

Wirrabel Boers and Dorper Sheep Stud Maree Dalton +61 412578304 Sandra Pollock +61 438615027 wirrabel5184@mailvane.com Tarrawong Victoria Australia

Colors
EE7325
F08F49
F5BC92
FAE3D3
FDF4ED

Requirements
Must have
• My Boer Goats and Dorper Sheep images see my photos

```html
<!DOCTYPE html>
<html lang="en">
<head>
<meta charset="utf-8">
<title>Wirrabel Boers and Dorper Sheep Stud – Business Card</title>
<link href="https://fonts.googleapis.com/css2?family=Oswald:wght@600&family=Arimo:wght@400&display=swap" rel="stylesheet">
<style>
  :root {
    --page-bg: #2b2b2b;
    --card-dark: #1f1f1f;
    --card-mid: #353535;
    --band: #4a4a4a;
    --ring: #5a5a5a;
    --text-light: #ffffff;
    --text-soft: #e6e6e6;
  }
  html, body {
    margin: 0;
    width: 1200px;
    height: 930px;
    overflow: hidden;
    background: var(--page-bg);
  }
  .canvas {
    position: relative;
    width: 1200px;
    height: 930px;
  }
  .card {
    position: absolute;
    left: 260px;
    width: 680px;
    height: 390px;
    border-radius: 18px;
    overflow: hidden;
    box-shadow: 0 10px 30px rgba(0,0,0,0.45);
  }
  /* Front */
  .card--front { top: 50px; }
  .front-photo {
    position: absolute;
    inset: 0;
    background:
      radial-gradient(ellipse at 55% 50%, #d8d2c8 0%, #b9a897 30%, transparent 60%),
      linear-gradient(135deg, #4f6b3a 0%, #6e5a45 35%, #8a5a38 55%, #5a4a3c 100%);
  }
  .front-shade {
    position: absolute;
    inset: 0;
    background: rgba(20, 20, 20, 0.42);
  }
  .front-title {
    position: absolute;
    left: 0;
    right: 0;
    top: 50%;
    transform: translateY(-50%);
    margin: 0;
    text-align: center;
    font-family: "Oswald", sans-serif;
    font-weight: 600;
    font-size: 40px;
    letter-spacing: 1px;
    color: var(--text-light);
    text-transform: uppercase;
  }
  /* Back */
  .card--back {
    top: 490px;
    background: linear-gradient(120deg, var(--card-dark) 0%, var(--card-mid) 45%, var(--card-dark) 100%);
  }
  .back-band {
    position: absolute;
    left: 0;
    top: 150px;
    width: 460px;
    height: 104px;
    background: linear-gradient(90deg, var(--band), #3c3c3c);
  }
  .sheep-ring {
    position: absolute;
    left: 355px;
    top: -20px;
    width: 430px;
    height: 430px;
    border-radius: 50%;
    background: var(--ring);
  }
  .sheep-photo {
    position: absolute;
    left: 369px;
    top: -6px;
    width: 402px;
    height: 402px;
    border-radius: 50%;
    background:
      radial-gradient(ellipse at 45% 55%, #f2eee6 0%, #e4ddd0 35%, transparent 62%),
      linear-gradient(160deg, #7a6a4c 0%, #5f8a3c 45%, #7fa650 100%);
  }
  .contacts {
    position: absolute;
    left: 34px;
    top: 66px;
    margin: 0;
    padding: 0;
    list-style: none;
    font-family: "Arimo", sans-serif;
    font-size: 18px;
    line-height: 28px;
    color: var(--text-soft);
  }
  .contacts .name { text-transform: uppercase; }
  .brand {
    position: absolute;
    left: 34px;
    top: 156px;
    margin: 0;
    font-family: "Oswald", sans-serif;
    font-weight: 600;
    color: var(--text-light);
    text-transform: uppercase;
    line-height: 1;
  }
  .brand__main { display: block; font-size: 48px; }
  .brand__sub { display: block; font-size: 29px; margin-top: 4px; }
  .details {
    position: absolute;
    left: 34px;
    top: 290px;
    margin: 0;
    font-family: "Arimo", sans-serif;
    font-size: 18px;
    line-height: 30px;
    color: var(--text-soft);
  }
  .details p { margin: 0; }
</style>
</head>
<body>
<div class="canvas">

  <section class="card card--front">
    <div class="front-photo" role="img" aria-label="Photo of Boer goats with brown heads and white bodies in a paddock"></div>
    <div class="front-shade"></div>
    <h1 class="front-title">Wirrabel Boers &amp; Dorper Sheep Stud</h1>
  </section>

  <section class="card card--back">
    <div class="back-band"></div>
    <div class="sheep-ring"></div>
    <div class="sheep-photo" role="img" aria-label="Photo of two Dorper sheep with black heads and white bodies on grass"></div>

    <ul class="contacts">
      <li><span class="name">Maree Dalton</span> +61 412578304</li>
      <li><span class="name">Sandra Pollock</span> +61 438615027</li>
    </ul>

    <h2 class="brand">
      <span class="brand__main">Wirrabel Boers</span>
      <span class="brand__sub">&amp; Dorper Sheep Stud</span>
    </h2>

    <div class="details">
      <p>E : wirrabel5184@mailvane.com</p>
      <p>A : Tarrawong Victoria Australia</p>
    </div>
  </section>

</div>
</body>
</html>
```